Brightway Haus Inc. Business Card Design

Brightway Haus Inc. is in search of a great clean design for our business cards!

Looking to incorporate our full logo and watermark on side one (however, I am open to having the text and watermark separated within the design.)

On side two, I am looking to have contact information (Name, Position, Phone #, Email, Website (www.thebrightwayhaus.ca). Can have the logo and/or watermark as part of the design if applicable.

Please add tagline "Where Shine Counts" on either side 1 or 2. This tagline can be in a sans serif, serif or cursive font as long as it compliments overall design. Capitalization can be title or sentence case depending on how it fits within the design.

Get creative!! Looking for a clean, crisp, premium design! Looking for a glossy card finish with spot UV features when printed. Cards will also be printed with rounded corners. Standard dimensions (3.5 x 2).

Target Market(s)

B2B - primary clients are business owners or property management corporations. (residential jobs are few and far between)

Industry/Entity Type

Business

Contact Information for Business Card

- clean, crisp design
- double sided
- spot UV accents and glossy finish upon printing
- standard business card size (3.5 x 2) with rounded corners
- please see project description for requirements per side

Font styles to use
Sans Serif

Requirements
Must have
• - adequate bleeds with print ready files
• - cohesive design elements between side 1 & 2
• - spot UV elements (can be on both sides or just one, use your discretion)
• - colour pallet should match the logo file provided
• - incorporate tagline "where shine counts" (this tagline can be in a serif or sans serif font as long as it is complimentary to the overall design.
Nice to have
• - Premium elements with a clean design
Should not have
• - Please omit cartoon or whimsical like designs, think premium.
• - Colours should not stray from the pallet of the provided logo.

```html
<!DOCTYPE html>
<html lang="en">
<head>
<meta charset="utf-8">
<title>Brightway Haus Inc. – Business Card</title>
<link href="https://fonts.googleapis.com/css2?family=Arimo:wght@400;700&display=swap" rel="stylesheet">
<style>
  :root {
    --navy: #1b2553;
    --navy-soft: #26335f;
    --teal: #1fb3b9;
    --ink: #3a3a42;
    --paper: #ffffff;
    --mist: #f3f3f5;
    --page: #e6e7ea;
  }
  * { box-sizing: border-box; margin: 0; padding: 0; }
  html, body { width: 1200px; height: 1200px; overflow: hidden; }
  body {
    background: var(--page);
    font-family: "Arimo", Arial, sans-serif;
    position: relative;
  }
  .card {
    position: absolute;
    left: 150px;
    width: 900px;
    height: 514px;
    overflow: hidden;
    box-shadow: 0 6px 18px rgba(0,0,0,.12);
  }
  /* Side one */
  .card-back {
    top: 50px;
    background: linear-gradient(135deg, var(--navy-soft) 0%, var(--navy) 55%, var(--navy) 100%);
  }
  .card-back .brand-name {
    position: absolute;
    left: 0; right: 0; top: 205px;
    text-align: center;
    color: var(--paper);
    font-weight: 700;
    font-size: 56px;
    letter-spacing: -1px;
  }
  .card-back .tagline {
    position: absolute;
    right: 60px; bottom: 50px;
    color: var(--paper);
    font-size: 26px;
    letter-spacing: 1px;
  }
  /* Side two */
  .card-front {
    top: 614px;
    background: linear-gradient(160deg, var(--mist) 0%, var(--paper) 40%);
  }
  .card-front .band {
    position: absolute; left: 0; top: 0;
    width: 900px; height: 514px;
  }
  .brand {
    position: absolute;
    left: 60px; top: 62px;
    display: flex; align-items: center; gap: 16px;
  }
  .brand-mark {
    width: 48px; height: 48px;
    background: var(--teal);
  }
  .brand .brand-name {
    color: var(--navy);
    font-weight: 700;
    font-size: 46px;
    letter-spacing: -1px;
  }
  .contact {
    position: absolute;
    left: 468px; top: 222px;
    padding-left: 16px;
    border-left: 2px solid var(--navy);
  }
  .person {
    font-weight: 700;
    font-size: 40px;
    letter-spacing: -0.5px;
  }
  .person .first { color: var(--teal); }
  .person .last { color: var(--navy); }
  .role {
    font-size: 22px;
    color: var(--ink);
    margin-top: 8px;
  }
  .details {
    list-style: none;
    margin-top: 16px;
  }
  .details li {
    display: flex; align-items: center; gap: 10px;
    font-size: 23px;
    color: var(--ink);
    line-height: 34px;
  }
  .details svg { width: 20px; height: 20px; flex: none; }
  .card-front .tagline {
    position: absolute;
    left: 60px; bottom: 30px;
    color: var(--paper);
    font-size: 26px;
    letter-spacing: 1px;
  }
</style>
</head>
<body>

  <section class="card card-back" aria-label="Business card, side one">
    <div class="brand-name">BRIGHTWAY HAUS INC.</div>
    <div class="tagline">Where Shine Counts</div>
  </section>

  <section class="card card-front" aria-label="Business card, side two">
    <svg class="band" viewBox="0 0 900 514" aria-hidden="true">
      <path d="M0 428 H300 C350 428 372 466 420 470 H900 V514 H0 Z" fill="var(--navy)"/>
    </svg>

    <div class="brand">
      <span class="brand-mark" aria-hidden="true"></span>
      <span class="brand-name">BRIGHTWAY HAUS INC.</span>
    </div>

    <div class="contact">
      <div class="person"><span class="first">ALEX</span> <span class="last">MORGAN</span></div>
      <div class="role">Director</div>
      <ul class="details">
        <li>
          <svg viewBox="0 0 20 20" aria-hidden="true"><path d="M5 2 L8 6 L6.5 8 C7.5 10.5 9.5 12.5 12 13.5 L14 12 L18 15 L16 18 C9 18 2 11 2 4 Z" fill="var(--teal)"/></svg>
          555-014-2290
        </li>
        <li>
          <svg viewBox="0 0 20 20" aria-hidden="true"><circle cx="10" cy="10" r="8" fill="none" stroke="var(--teal)" stroke-width="2"/><path d="M2 10 H18 M10 2 C6 6 6 14 10 18 M10 2 C14 6 14 14 10 18" fill="none" stroke="var(--teal)" stroke-width="1.5"/></svg>
          www.thebrightwayhaus.ca
        </li>
        <li>
          <svg viewBox="0 0 20 20" aria-hidden="true"><rect x="1" y="4" width="18" height="13" fill="var(--teal)"/></svg>
          info@brightwayhaus.ca
        </li>
      </ul>
    </div>

    <div class="tagline">Where Shine Counts</div>
  </section>

</body>
</html>
```